Fence Contractor Website Design

We are working with Yard Shield. They are a local fencing and automatic gate installer and in need of a new website design.
Some sites to use for inspiration:
https://pelmorfence.example
https://tarvikfence.example
https://www.bristowdecksandfence.example
https://www.railquestinc.example
Thank you for taking the time to consider designing a website for us. We are web developers based in Stockton, CA, USA. Most of our projects go through the same process. Understanding this process may help you win a project with us. We custom-code all of our websites in-house. We don’t have any requirements as to what tools you use for your design, but we prefer Figma files. For any design that we label as four-stars, we send it to the client for review. The client picks the final design they want us to use. Once we complete this process, we will continue to show additional clients all the four-star sites and purchase them later. Your designs will have multiple chances to sell. For better chances of success, we ask that you follow these guidelines.
IMAGES:
If you use any images or icons in the design, we ask that you have a link to the asset so we can purchase the image/icon. Most of the designs we submit do not have the customer’s images on them unless they have some great images. Be creative; show us the feeling you are trying to portray with your image choices. Use any royalty-free site you choose. We subscribe to Veltrix and mainly use their images, but we can purchase images outside of Veltrix.
PLEASE NOTE: we will not submit designs to clients with watermarks on the images.
FONTS:
We ask that you identify the fonts used in the design. This can be done in a message if you want. We typically use Google Fonts and Veltrix Fonts.
CONTENT:
We're always open to different content and ideas. We often submit designs with stock images so the client can see our vision. We typically take pictures after the website launch to use their images with our vision. Lorem Ipsum is fine for paragraphs, but we ask that you write the headers in correct English. We want to be able to show the vision and identify the sections of the website.
INSPIRATION:
We typically add a couple of links in the brief of websites we like to help you get started in your design.
REVISIONS:
We do not often ask for revisions of the designs unless we see something in the design that may not appeal to the client. If there are slight changes that we want to make, we do that in the development process.
FEEDBACK:
We rarely give feedback on designs during the design process. We are working on many website projects and do not have the time to provide feedback. We usually respond if your request is well thought out and asks specific questions, but a note asking “feedback, please” usually goes unanswered.

```html
<!DOCTYPE html>
<html lang="en">
<head>
<meta charset="utf-8">
<title>Yard Shield — Fencing &amp; Gates</title>
<link href="https://fonts.googleapis.com/css2?family=Montserrat:wght@400;500;600;700&display=swap" rel="stylesheet">
<style>
:root{
  --navy:#151c38;
  --red:#ec1c24;
  --ink:#1b1f2e;
  --muted:#5b5f6b;
  --white:#ffffff;
  --black:#121212;
  --hex:#e6e7ea;
}
*{margin:0;padding:0;box-sizing:border-box}
html,body{width:1200px;height:4777px;overflow:hidden}
body{position:relative;font-family:"Montserrat",sans-serif;color:var(--ink);background:var(--white)}
.abs{position:absolute}
.center{left:0;width:1200px;text-align:center}
.btn{position:absolute;display:flex;align-items:center;justify-content:center;font-size:14px;font-weight:500;text-transform:uppercase;border-radius:4px;background:var(--red);color:var(--white)}
.btn--outline{background:var(--white);color:var(--ink);border:1.5px solid var(--red)}
.section-title{position:absolute;font-size:31px;font-weight:600;text-transform:uppercase;letter-spacing:-.5px}
.title-mark{position:absolute;width:36px;height:12px}

/* header */
.site-header{position:absolute;top:0;left:0;width:1200px;height:82px;background:var(--white);border-top:3px solid var(--red);z-index:3}
.brand{position:absolute;left:111px;top:26px;display:flex;align-items:center;gap:8px;font-size:20px;font-weight:700;color:var(--navy);text-transform:uppercase}
.brand i{display:block;width:14px;height:14px;background:var(--red)}
.nav a{position:absolute;top:32px;font-size:14px;font-weight:500;text-transform:uppercase;color:var(--ink);text-decoration:none}
.nav a.is-active{color:var(--red)}

/* hero */
.hero{position:absolute;top:82px;left:0;width:1200px;height:563px;overflow:hidden}
.hero-photo{position:absolute;inset:0;background:linear-gradient(100deg,#7a4a26 0%,#9a6236 28%,#4a4c3a 55%,#6d6b5e 80%,#a29c8c 100%)}
.hero-shade{position:absolute;inset:0;background:rgba(0,0,0,.28)}
.hero h1{position:absolute;top:193px;font-size:40px;font-weight:600;color:var(--white);text-transform:uppercase;letter-spacing:-1px}
.hero p{position:absolute;top:264px;font-size:18px;color:var(--white)}

/* services */
.service-card{position:absolute;top:768px;width:306px;height:384px;background:var(--white);box-shadow:0 2px 10px rgba(0,0,0,.12)}
.service-photo{position:absolute;left:0;top:0;width:306px;height:187px}
.service-card h3{position:absolute;top:222px;left:0;width:100%;text-align:center;font-size:17px;font-weight:600;text-transform:uppercase;letter-spacing:-.3px}
.service-card p{position:absolute;top:258px;left:30px;width:246px;text-align:center;font-size:14px;line-height:34px;color:var(--muted)}

/* about */
.about{position:absolute;top:1332px;left:0;width:1200px;height:686px;background:var(--navy)}
.about h2{color:var(--white);top:70px;left:111px}
.about p{position:absolute;left:111px;width:470px;font-size:14px;line-height:34.5px;color:var(--white)}

/* why */
.why-head{position:absolute;font-size:19px;font-weight:600;text-transform:uppercase;line-height:37px}
.why-text{position:absolute;font-size:14px;line-height:34px;color:var(--muted)}
.why-icon{position:absolute;width:74px;height:74px;border-radius:50%;background:var(--navy);border:4px solid var(--white);box-shadow:0 0 0 1px #d0d2d8;display:flex;align-items:center;justify-content:center}
.why-icon--red{background:var(--red)}

/* portfolio */
.portfolio{position:absolute;top:2942px;left:0;width:1200px;height:963px;background:var(--navy)}
.tile{position:absolute}

/* reviews */
.quote{position:absolute;top:4124px;left:180px;width:840px;text-align:center;font-size:14.5px;line-height:35px;color:var(--ink)}
.dot{position:absolute;top:4304px;width:9px;height:9px;border-radius:50%;border:1.5px solid var(--red)}

/* footer */
.site-footer{position:absolute;top:4396px;left:0;width:1200px;height:381px;background:var(--black);color:var(--white)}
.footer-brand{position:absolute;left:130px;top:124px;display:flex;align-items:center;gap:10px;font-size:26px;font-weight:700;text-transform:uppercase;color:var(--white)}
.footer-brand i{display:block;width:18px;height:18px;background:var(--red)}
.footer-col h4{position:absolute;top:52px;font-size:17px;font-weight:500;color:var(--red);text-transform:uppercase}
.footer-col a{position:absolute;font-size:13px;color:var(--white);text-decoration:none;text-transform:uppercase}
.copyright{position:absolute;top:340px;left:0;width:1200px;text-align:center;font-size:12.5px;text-transform:uppercase}
</style>
</head>
<body>

<!-- Header -->
<header class="site-header">
  <div class="brand"><i></i>Yard Shield</div>
  <nav class="nav">
    <a class="is-active" style="left:409px">Home</a>
    <a style="left:491px">About Us</a>
    <a style="left:606px">Services</a>
    <a style="left:716px">Gallery</a>
    <a style="left:824px">Contact Us</a>
  </nav>
  <span class="btn" style="left:963px;top:21px;width:126px;height:37px;font-size:13px">Get a Quote</span>
</header>

<!-- Hero -->
<section class="hero">
  <div class="hero-photo" role="img" aria-label="Wooden privacy fence beside a black automatic driveway gate"></div>
  <div class="hero-shade"></div>
  <h1 class="center">Secure Fences. Smarter Gates.</h1>
  <p class="center">Trusted local experts for residential &amp; commercial installations.</p>
  <span class="btn" style="left:464px;top:333px;width:272px;height:39px">Schedule a Consultation</span>
  <svg class="abs" style="left:0;top:0" width="1200" height="563" viewBox="0 0 1200 563">
    <polygon points="0,563 599,480 1200,563" fill="var(--navy)"/>
    <polygon points="0,563 599,500 1200,563" fill="var(--white)"/>
  </svg>
</section>

<!-- Services -->
<h2 class="section-title center" style="top:661px">Our Services</h2>
<svg class="title-mark" style="left:582px;top:705px" viewBox="0 0 36 12"><polygon points="0,0 14,0 18,12" fill="var(--navy)"/><polygon points="36,0 22,0 18,12" fill="var(--navy)"/><rect x="15" y="0" width="6" height="8" fill="var(--red)"/></svg>

<article class="service-card" style="left:111px">
  <div class="service-photo" role="img" aria-label="Installer fitting a metal fence panel" style="background:linear-gradient(135deg,#2b3140,#56627a 60%,#8a92a0)"></div>
  <svg class="abs" style="left:0;top:160px" width="306" height="32"><polygon points="0,27 153,12 306,27 306,32 0,32" fill="var(--white)"/><polyline points="0,27 153,12 306,27" fill="none" stroke="var(--red)" stroke-width="3"/></svg>
  <h3>Fence Installation</h3>
  <p>Wood, vinyl, chain link, aluminum, and ornamental iron options for residential</p>
</article>
<article class="service-card" style="left:447px">
  <div class="service-photo" role="img" aria-label="Modern wooden sliding gate with keypad" style="background:linear-gradient(135deg,#8fb3d9,#b9c6cf 40%,#7a3a26 70%,#5d2c1e)"></div>
  <svg class="abs" style="left:0;top:160px" width="306" height="32"><polygon points="0,27 153,12 306,27 306,32 0,32" fill="var(--white)"/><polyline points="0,27 153,12 306,27" fill="none" stroke="var(--red)" stroke-width="3"/></svg>
  <h3>Automatic Gates &amp; Control</h3>
  <p>Sliding and swing gates keypad, remote, and smart-access systems</p>
</article>
<article class="service-card" style="left:783px">
  <div class="service-photo" role="img" aria-label="Cordless drill repairing a fence panel" style="background:linear-gradient(135deg,#cfd8cf,#8aa08a 45%,#a33030 70%,#3b3b3b)"></div>
  <svg class="abs" style="left:0;top:160px" width="306" height="32"><polygon points="0,27 153,12 306,27 306,32 0,32" fill="var(--white)"/><polyline points="0,27 153,12 306,27" fill="none" stroke="var(--red)" stroke-width="3"/></svg>
  <h3>Fence &amp; Gate Repairs</h3>
  <p>Fast, reliable repair services storm damage, wear &amp; tear, or accident repairs</p>
</article>

<span class="btn" style="left:436px;top:1206px;width:165px;height:42px">View Services</span>
<span class="btn btn--outline" style="left:620px;top:1206px;width:142px;height:42px">Learn More</span>

<svg class="abs" style="left:0;top:1260px" width="80" height="73"><polygon points="0,0 74,73 0,73" fill="var(--navy)"/></svg>

<!-- About -->
<section class="about">
  <h2 class="section-title" style="top:70px;left:111px;color:var(--white)">About Yard Shield</h2>
  <svg class="title-mark" style="left:111px;top:120px" viewBox="0 0 36 12"><polygon points="0,0 14,0 18,12" fill="var(--white)"/><polygon points="36,0 22,0 18,12" fill="var(--white)"/><rect x="15" y="0" width="6" height="8" fill="var(--red)"/></svg>
  <p style="top:154px">At Yard Shield, we believe every property deserves the perfect balance of security, privacy, and style. As a trusted local fencing and automatic gate installer, we've built our reputation on quality craftsmanship, reliable service, and solutions that stand the test of time.</p>
  <p style="top:342px">With years of experience serving homeowners and businesses, our team handles everything from simple backyard fences to fully automated gate systems. Whether you need added security, curb appeal, or both, Yard Shield is committed to delivering work you can count on.</p>
  <span class="btn" style="left:111px;top:560px;width:147px;height:41px">Learn More</span>
  <div class="abs" role="img" aria-label="White vinyl picket fence along a green lawn" style="left:638px;top:76px;width:310px;height:490px;background:linear-gradient(160deg,#3f6e3a,#6f9a5a 35%,#e9ecef 55%,#4f8a3a 85%)"></div>
  <div class="abs" role="img" aria-label="Black metal fence in front of a hedge" style="left:987px;top:132px;width:213px;height:471px;background:linear-gradient(170deg,#9fb0bd,#5c7a4a 40%,#2a2f2c 70%,#8d8d86)"></div>
</section>

<!-- Why choose us -->
<h2 class="section-title center" style="top:2095px">Why Choose Us</h2>
<svg class="title-mark" style="left:582px;top:2140px" viewBox="0 0 36 12"><polygon points="0,0 14,0 18,12" fill="var(--navy)"/><polygon points="36,0 22,0 18,12" fill="var(--navy)"/><rect x="15" y="0" width="6" height="8" fill="var(--red)"/></svg>

<div class="why-head center" style="top:2188px">Local &amp; Trusted</div>
<div class="why-text center" style="top:2226px">Proudly serving our community with reliable, friendly service.</div>

<svg class="abs" style="left:417px;top:2318px" width="366" height="446" viewBox="0 0 366 446"><polygon points="183,0 366,110 366,336 183,446 0,336 0,110" fill="var(--hex)"/></svg>
<div class="abs" style="left:427px;top:2510px;width:346px;text-align:center;font-size:34px;font-weight:700;color:var(--navy);text-transform:uppercase">Yard Shield</div>

<div class="why-icon" style="left:562px;top:2282px"><svg width="30" height="30" viewBox="0 0 30 30" fill="none" stroke="#fff" stroke-width="2"><circle cx="15" cy="15" r="11"/><path d="M9 15l4 4 8-8"/></svg></div>
<div class="why-icon" style="left:358px;top:2395px"><svg width="30" height="30" viewBox="0 0 30 30" fill="none" stroke="#fff" stroke-width="2"><circle cx="15" cy="13" r="5"/><path d="M6 26c2-6 16-6 18 0"/></svg></div>
<div class="why-icon why-icon--red" style="left:755px;top:2399px"><svg width="30" height="30" viewBox="0 0 30 30" fill="none" stroke="#fff" stroke-width="2"><circle cx="15" cy="15" r="10"/><circle cx="15" cy="15" r="4"/></svg></div>
<div class="why-icon" style="left:367px;top:2606px"><svg width="30" height="30" viewBox="0 0 30 30" fill="none" stroke="#fff" stroke-width="2"><path d="M8 27V15h4l5-9c2 0 3 2 2 5l-1 4h7l-2 12z"/></svg></div>
<div class="why-icon" style="left:759px;top:2606px"><svg width="30" height="30" viewBox="0 0 30 30" fill="none" stroke="#fff" stroke-width="2"><path d="M6 22l10-10 4 4-10 10H6z"/><path d="M18 8l4 4"/></svg></div>
<div class="why-icon" style="left:562px;top:2703px"><svg width="30" height="30" viewBox="0 0 30 30" fill="none" stroke="#fff" stroke-width="2"><rect x="6" y="6" width="14" height="18"/><circle cx="20" cy="19" r="5"/><path d="M24 23l4 4"/></svg></div>

<div class="why-head" style="left:120px;top:2390px;width:214px;text-align:right">Automatic Gate Specialists</div>
<div class="why-text" style="left:130px;top:2468px;width:204px;text-align:right">Advanced technology for convenience, safety, and security.</div>
<div class="why-head" style="left:866px;top:2390px;width:200px;color:var(--red)">Expert Installation</div>
<div class="why-text" style="left:866px;top:2468px;width:240px">Professional, licensed installers who get it right the first time.</div>
<div class="why-head" style="left:120px;top:2602px;width:214px;text-align:right">Guaranteed Satisfaction</div>
<div class="why-text" style="left:110px;top:2680px;width:224px;text-align:right">Clear communication, fair pricing, and results you'll love.</div>
<div class="why-head" style="left:866px;top:2602px;width:200px">Custom Solutions</div>
<div class="why-text" style="left:866px;top:2680px;width:224px">Fences and gates designed to fit your style, property, and budget.</div>

<div class="why-head center" style="top:2797px">Quality Materials</div>
<div class="why-text center" style="top:2838px">We source only durable, industry-proven products.</div>

<svg class="abs" style="left:1120px;top:2868px" width="80" height="75"><polygon points="80,0 80,75 6,75" fill="var(--navy)"/></svg>

<!-- Portfolio -->
<section class="portfolio">
  <h2 class="section-title center" style="top:56px;color:var(--white)">Yard Shield Portfolio</h2>
  <svg class="title-mark" style="left:582px;top:109px" viewBox="0 0 36 12"><polygon points="0,0 14,0 18,12" fill="var(--white)"/><polygon points="36,0 22,0 18,12" fill="var(--white)"/><rect x="15" y="0" width="6" height="8" fill="var(--red)"/></svg>
  <div class="tile" role="img" aria-label="White picket fence with flower beds" style="left:111px;top:169px;width:572px;height:317px;background:linear-gradient(170deg,#a9c3d9,#e7eaec 45%,#c0407a 70%,#4f8a3a)"></div>
  <div class="tile" role="img" aria-label="Black gate over a paved driveway" style="left:705px;top:169px;width:384px;height:317px;background:linear-gradient(175deg,#6d7a5a,#2a2d2e 45%,#4a4c55 80%)"></div>
  <div class="tile" role="img" aria-label="Welded wire security fence" style="left:111px;top:514px;width:312px;height:284px;background:linear-gradient(175deg,#4c5058,#8a8d90 55%,#d7d1c4)"></div>
  <div class="tile" role="img" aria-label="Ornamental wrought iron gate detail" style="left:445px;top:514px;width:312px;height:284px;background:linear-gradient(135deg,#1d1f24,#6b5a4a 50%,#c9c4bb)"></div>
  <div class="tile" role="img" aria-label="Chain link fence at sunset" style="left:777px;top:514px;width:312px;height:284px;background:linear-gradient(135deg,#3a3b4c,#9a6a54 55%,#1c1c22)"></div>
  <span class="btn" style="left:486px;top:846px;width:225px;height:43px">View More Portfolio</span>
</section>

<!-- Reviews -->
<h2 class="section-title center" style="top:3979px">Customer Reviews</h2>
<svg class="title-mark" style="left:582px;top:4024px" viewBox="0 0 36 12"><polygon points="0,0 14,0 18,12" fill="var(--navy)"/><polygon points="36,0 22,0 18,12" fill="var(--navy)"/><rect x="15" y="0" width="6" height="8" fill="var(--red)"/></svg>
<svg class="abs" style="left:534px;top:4078px" width="132" height="24" viewBox="0 0 132 24">
  <g fill="#f5b921" stroke="#3a2a00" stroke-width="1">
    <polygon points="12,1 15,9 23,9 17,14 19,22 12,17 5,22 7,14 1,9 9,9"/>
    <polygon transform="translate(27 0)" points="12,1 15,9 23,9 17,14 19,22 12,17 5,22 7,14 1,9 9,9"/>
    <polygon transform="translate(54 0)" points="12,1 15,9 23,9 17,14 19,22 12,17 5,22 7,14 1,9 9,9"/>
    <polygon transform="translate(81 0)" points="12,1 15,9 23,9 17,14 19,22 12,17 5,22 7,14 1,9 9,9"/>
    <polygon transform="translate(108 0)" points="12,1 15,9 23,9 17,14 19,22 12,17 5,22 7,14 1,9 9,9"/>
  </g>
</svg>
<p class="quote">"Yard Shield transformed our backyard with a beautiful wood fence. The crew was professional, quick, and left everything spotless. Couldn't be happier! Our new automatic gate is a game changer. Smooth install, easy to use, and it looks amazing. Yard Shield really knows their craft."</p>
<div class="abs center" style="top:4249px;font-size:14.5px;font-weight:500;text-transform:uppercase"><span style="color:var(--red)">Marcus T.,</span> Business Owner</div>
<span class="dot" style="left:544px;background:var(--red)"></span>
<span class="dot" style="left:570px"></span>
<span class="dot" style="left:596px"></span>
<span class="dot" style="left:621px"></span>
<span class="dot" style="left:647px"></span>

<svg class="abs" style="left:0;top:4322px" width="80" height="75"><polygon points="0,0 74,75 0,75" fill="var(--black)"/></svg>

<!-- Footer -->
<footer class="site-footer">
  <div class="footer-brand"><i></i>Yard Shield</div>
  <div class="footer-col">
    <h4 style="left:503px">Company</h4>
    <a style="left:503px;top:102px">About Us</a>
    <a style="left:503px;top:139px">Services</a>
    <a style="left:503px;top:176px">Reviews</a>
    <a style="left:503px;top:215px">Capabilities</a>
    <a style="left:503px;top:252px">Manufacturing Resources</a>
  </div>
  <div class="footer-col">
    <h4 style="left:870px">Support</h4>
    <a style="left:870px;top:102px">Contact Us</a>
    <a style="left:870px;top:139px">Request a Quote</a>
    <a style="left:870px;top:176px">FAQs</a>
    <a style="left:870px;top:215px">Download Line Card (PDF)</a>
  </div>
  <div class="copyright">Copyright © 2025 Yard Shield - All Rights Reserved</div>
</footer>

</body>
</html>
```